Brightmill Data Works

Our company is about IT hardwares and IT solutions. IT hardware such as PC, RAMS, storage and servers. IT solutions such as project management, BA. We are also selling new technology too.

Target Market(s)

Consumer, Small to Medium Business, Corporate

Requirements
Must have
• The business card must have the following:
• Name:
• Title:
• Contact Number:
• Email address:
• Website:
• Color: Must match the logo color upgrade

```html
<!DOCTYPE html>
<html lang="en">
<head>
<meta charset="UTF-8">
<title>Brightmill Data Works – Business Card</title>
<link rel="stylesheet" href="https://fonts.googleapis.com/css2?family=Lato:wght@400;700&display=swap">
<style>
  :root {
    --page-bg: #e9e6e3;
    --card-charcoal: #494949;
    --accent-orange: #c8692a;
    --name-orange: #e08a2e;
    --disc-white: #f4f2f0;
    --text-light: #f2f2f2;
    --text-dark: #3d3d3d;
  }
  * { margin: 0; padding: 0; box-sizing: border-box; }
  html, body {
    width: 1200px; height: 900px; overflow: hidden;
    background: var(--page-bg);
    font-family: "Lato", Arial, sans-serif;
  }
  .business-card {
    position: absolute; left: 120px; top: 155px;
    width: 960px; height: 590px;
    border-radius: 16px; overflow: hidden;
    background: var(--card-charcoal);
    box-shadow: 0 18px 40px rgba(0,0,0,0.18);
  }
  .accent-band {
    position: absolute; top: 0; right: 0; bottom: 0;
    width: 309px; background: var(--accent-orange);
  }
  .brand-disc {
    position: absolute; left: 380px; top: 15px;
    width: 550px; height: 550px; border-radius: 50%;
    background: var(--disc-white);
    box-shadow: 0 4px 18px rgba(0,0,0,0.18);
    display: flex; flex-direction: column; align-items: center; justify-content: center;
    gap: 26px;
  }
  .brand-dot {
    width: 64px; height: 64px; border-radius: 50%;
    background: var(--accent-orange);
  }
  .brand-name {
    font-weight: 700; font-size: 52px; line-height: 1.05;
    letter-spacing: 2px; text-transform: uppercase; text-align: center;
    color: var(--text-dark);
  }
  .holder {
    position: absolute; left: 56px; top: 88px;
  }
  .holder-name {
    font-size: 33px; font-weight: 400; letter-spacing: 0.5px;
    text-transform: uppercase; color: var(--name-orange);
  }
  .holder-title {
    margin-top: 4px; font-size: 26px; color: var(--text-light);
  }
  .contact-list {
    position: absolute; left: 56px; top: 395px;
    list-style: none;
  }
  .contact-item {
    display: flex; align-items: center; gap: 12px;
    font-size: 25px; color: var(--text-light);
    height: 35px;
  }
  .contact-icon { width: 20px; height: 20px; fill: var(--name-orange); flex: none; }
</style>
</head>
<body>
  <main class="business-card">
    <div class="accent-band"></div>

    <div class="holder">
      <p class="holder-name">Daniel Harper</p>
      <p class="holder-title">Managing Director</p>
    </div>

    <ul class="contact-list">
      <li class="contact-item">
        <svg class="contact-icon" viewBox="0 0 20 20" aria-hidden="true">
          <path d="M2 6c0-2 3-3.5 8-3.5S18 4 18 6v1.5h-4V6H6v1.5H2z"/>
          <path d="M5 9h10l3 8H2z"/>
        </svg>
        044-555 210 347
      </li>
      <li class="contact-item">
        <svg class="contact-icon" viewBox="0 0 20 20" aria-hidden="true">
          <path d="M1 4h18v1.5l-9 6-9-6z"/>
          <path d="M1 7.5l9 6 9-6V16H1z"/>
        </svg>
        info@brightmilldata.com
      </li>
      <li class="contact-item">
        <svg class="contact-icon" viewBox="0 0 20 20" aria-hidden="true">
          <circle cx="10" cy="10" r="9"/>
          <path d="M6 5c2 1 3 0 4 2s-2 3-1 5 3 1 2 4M14 4c-1 2 1 3 3 3" stroke="var(--card-charcoal)" stroke-width="1.4" fill="none"/>
        </svg>
        www.brightmilldata.com
      </li>
    </ul>

    <div class="brand-disc">
      <span class="brand-dot"></span>
      <p class="brand-name">Brightmill<br>Data Works</p>
    </div>
  </main>
</body>
</html>
```